Rollers & Glides.com

Vertical Business Card with focus on branding with our icon. Information on card will be logo, persons name, position, phone number, email address and website. Use the the name Marcus Pellow, position President, phone number 480.915.2267, email Marcus@rollersandglides-demo.com, website www.rollersandglides-demo.com.

```html
<!DOCTYPE html>
<html lang="en">
<head>
<meta charset="UTF-8">
<title>Rollers &amp; Glides.com — Business Card</title>
<link rel="stylesheet" href="https://fonts.googleapis.com/css2?family=Lato:wght@400;700;900&display=swap">
<style>
  :root {
    --stage: #1c1c1f;
    --card-white: #ffffff;
    --brand-blue: #2f6cc4;
    --brand-blue-deep: #1d4fc0;
    --brand-blue-light: #3a7ad6;
    --title-grey: #8a8a8a;
  }
  * { margin: 0; padding: 0; box-sizing: border-box; }
  html, body {
    width: 1200px;
    height: 900px;
    overflow: hidden;
    background: var(--stage);
    font-family: "Lato", sans-serif;
  }
  .stage {
    width: 1200px;
    height: 900px;
    display: flex;
    align-items: center;
    justify-content: center;
    gap: 60px;
  }
  .card {
    width: 400px;
    height: 700px;
    border-radius: 4px;
    position: relative;
    overflow: hidden;
  }
  .card-front {
    background: var(--card-white);
    padding: 64px 48px 60px;
    display: flex;
    flex-direction: column;
  }
  .person-name {
    font-weight: 900;
    font-size: 30px;
    letter-spacing: 1px;
    text-transform: uppercase;
    color: var(--brand-blue);
    line-height: 1.1;
  }
  .person-title {
    font-weight: 700;
    font-size: 24px;
    color: var(--title-grey);
    margin-top: 4px;
  }
  .brand-lockup {
    flex: 1;
    display: flex;
    flex-direction: column;
    align-items: center;
    justify-content: center;
    gap: 18px;
  }
  .brand-dot {
    width: 120px;
    height: 120px;
    border-radius: 50%;
    background: var(--brand-blue);
  }
  .brand-name {
    font-weight: 900;
    font-size: 28px;
    color: var(--brand-blue);
    text-align: center;
  }
  .contact-list {
    list-style: none;
    color: var(--brand-blue);
    align-self: flex-end;
    text-align: left;
  }
  .contact-phone {
    font-size: 30px;
    font-weight: 400;
    margin-bottom: 14px;
  }
  .contact-line {
    font-size: 16px;
    font-weight: 400;
    line-height: 1.45;
  }
  .card-back {
    background: linear-gradient(160deg, var(--brand-blue-light), var(--brand-blue-deep));
  }
</style>
</head>
<body>
  <main class="stage">
    <section class="card card-front">
      <h1 class="person-name">Marcus Pellow</h1>
      <p class="person-title">President</p>

      <div class="brand-lockup">
        <span class="brand-dot"></span>
        <p class="brand-name">Rollers &amp; Glides.com</p>
      </div>

      <ul class="contact-list">
        <li class="contact-phone">480.915.2267</li>
        <li class="contact-line">Marcus@rollersandglides-demo.com</li>
        <li class="contact-line">www.rollersandglides-demo.com</li>
      </ul>
    </section>

    <section class="card card-back" role="img" aria-label="Card back: repeating brand icon pattern in blue tones"></section>
  </main>
</body>
</html>
```